Business Card Design Can you design a business card design? Looking for something unique and differe

Can you design a business card design? Looking for something unique and different. Can you design a business card design? Looking for something unique and different.Can you design a business card design? Looking for something unique and different.Can you design a business card design? Looking for something unique and different.Can you design a business card design? Looking for something unique and different.Can you design a business card design? Looking for something unique and different.

Industry/Entity Type

Business

Contact Information for Business Card

Can you design a business card design? Looking for something unique and different.

Font styles to use
Serif

```html
<!DOCTYPE html>
<html lang="en">
<head>
<meta charset="utf-8">
<title>Dosewell – Business Card</title>
<link href="https://fonts.googleapis.com/css2?family=Comfortaa:wght@700&family=Open+Sans:ital,wght@0,400;1,400&display=swap" rel="stylesheet">
<style>
  :root {
    --page-bg: #e9e6e3;
    --card-top: #f4f2f1;
    --card-bottom: #e6e3e2;
    --brand-purple: #6d5a80;
    --band-purple: #6e5783;
    --band-purple-light: #8a78a0;
    --band-black: #121114;
    --ink: #1d1b1f;
    --ink-soft: #3a3640;
    --muted: #77737a;
    --on-band: #d9d0e4;
  }
  * { box-sizing: border-box; margin: 0; padding: 0; }
  html, body { width: 1200px; height: 970px; overflow: hidden; }
  body { background: var(--page-bg); position: relative; }

  .business-card {
    position: absolute;
    left: 172px; top: 247px;
    width: 856px; height: 475px;
    background: linear-gradient(160deg, var(--card-top), var(--card-bottom));
    border-radius: 3px;
    box-shadow: 0 10px 30px rgba(60, 50, 70, 0.18);
    overflow: hidden;
  }

  .brand {
    position: absolute;
    left: 75px; top: 98px;
    width: 290px;
    text-align: center;
  }
  .brand-dot {
    display: block;
    width: 96px; height: 96px;
    margin: 0 auto 60px;
    border-radius: 50%;
    background: var(--brand-purple);
  }
  .brand-name {
    font-family: "Comfortaa", sans-serif;
    font-weight: 700;
    font-size: 44px;
    letter-spacing: 0.5px;
    color: var(--brand-purple);
    line-height: 1;
  }
  .brand-tagline {
    display: flex; align-items: center; justify-content: center;
    gap: 8px;
    margin-top: 10px;
    font-family: "Open Sans", sans-serif;
    font-size: 11px;
    letter-spacing: 4px;
    color: var(--muted);
  }
  .brand-tagline::before, .brand-tagline::after {
    content: ""; width: 40px; height: 1px; background: var(--muted);
  }

  .person {
    position: absolute; left: 461px; top: 60px;
  }
  .person-name {
    font-family: "Comfortaa", sans-serif;
    font-weight: 700;
    font-size: 25px;
    color: var(--brand-purple);
  }
  .person-role {
    margin-top: 10px;
    font-family: "Open Sans", sans-serif;
    font-style: italic;
    font-size: 16px;
    color: var(--ink-soft);
  }

  .contact-list {
    position: absolute; left: 461px; top: 190px;
    list-style: none;
    font-family: "Open Sans", sans-serif;
    font-size: 19px;
    color: var(--ink);
  }
  .contact-list li {
    display: flex; align-items: center;
    height: 29px;
  }
  .contact-icon {
    width: 18px; height: 18px;
    margin-right: 22px;
    fill: var(--ink-soft);
  }

  .address {
    position: absolute; left: 461px; top: 317px;
    font-family: "Open Sans", sans-serif;
    font-size: 19px;
    line-height: 29px;
    color: var(--ink);
  }

  .footer-bands { position: absolute; left: 0; bottom: 0; width: 856px; height: 61px; }
  .website {
    position: absolute; left: 461px; bottom: 19px;
    font-family: "Open Sans", sans-serif;
    font-size: 19px;
    color: var(--on-band);
  }
</style>
</head>
<body>
  <div class="business-card">
    <div class="brand">
      <span class="brand-dot"></span>
      <div class="brand-name">Dosewell</div>
      <div class="brand-tagline">cost management</div>
    </div>

    <div class="person">
      <div class="person-name">Your Long Name</div>
      <div class="person-role">Managing Director</div>
    </div>

    <ul class="contact-list">
      <li>
        <svg class="contact-icon" viewBox="0 0 20 20" aria-hidden="true">
          <path d="M2 6c0-2 3-3 8-3s8 1 8 3v2h-4V6.5c-1-.5-2.5-.7-4-.7s-3 .2-4 .7V8H2z"/>
          <path d="M5 9h10l2 8H3z"/>
        </svg>
        00.00.00.0000
      </li>
      <li>
        <svg class="contact-icon" viewBox="0 0 20 20" aria-hidden="true">
          <path d="M1 4h18v12H1z M2.5 5.5 10 11l7.5-5.5" stroke="#f2f0ef" stroke-width="1.2"/>
        </svg>
        11-2222-33334
      </li>
      <li>
        <svg class="contact-icon" viewBox="0 0 20 20" aria-hidden="true">
          <circle cx="10" cy="10" r="8"/>
          <path d="M2 10h16M10 2c-3 3-3 13 0 16M10 2c3 3 3 13 0 16" stroke="#f2f0ef" stroke-width="1.1" fill="none"/>
        </svg>
        yourname@yourwebsite.com
      </li>
    </ul>

    <div class="address">
      Your Commercial or office address<br>
      in just two line with pincode
    </div>

    <svg class="footer-bands" viewBox="0 0 856 61" aria-hidden="true">
      <defs>
        <linearGradient id="band-purple-fill" x1="0" x2="1" y1="0" y2="0">
          <stop offset="0" stop-color="var(--band-purple)"/>
          <stop offset="0.6" stop-color="var(--band-purple-light)"/>
          <stop offset="1" stop-color="var(--band-purple)"/>
        </linearGradient>
      </defs>
      <rect x="0" y="30" width="420" height="31" fill="var(--band-black)"/>
      <polygon points="428,0 856,0 856,61 386,61" fill="url(#band-purple-fill)"/>
    </svg>
    <div class="website">www.yourwebsite.com</div>
  </div>
</body>
</html>
```